Federal IT Consulting Company - Brisolux Consulting Group

We're seeking a skilled web designer to create a modern, bold, and engaging WordPress website for Brisolux Consulting Group, LLC. Our company specializes in federal IT consulting, and our name is a play on "Brightening Solutions." The website should reflect our expertise in the federal technology marketplace and position us as a trusted partner for clients navigating their IT journey.

contact: info@brisoluxgrp-example.com

Current Status

WordPress is already installed on our hosting account
We have an existing logo (may need modernization)

Design Requirements

Style:

Modern and visually striking design
Bold elements to convey confidence and expertise
Incorporate the concept of "brightening solutions" into the design

Features:

Modern UX sliders for dynamic content presentation
Eye-catching, high-quality images (stock photos to be sourced by the designer)
Responsive design for all devices

Color Scheme:

To be proposed by the designer, should align with our brand and convey trust and technological expertise

Logo:

Evaluate our current logo
Create a transparent background version if needed
Propose modernization if deemed necessary

Accessibility:

Ensure design elements are accessible to users with disabilities
Use high contrast ratios for text and background colors
Provide text alternatives for non-text content

Website Structure
Create the following pages, with the possibility of subpages:

Home
Services
About
Contact

Specific Page Requirements
Home Page

Striking hero section with a clear value proposition
Overview of our services
Client testimonials or trust indicators

Services Page

Detailed list of our IT consulting services
Clear explanation of how we help navigate the federal IT landscape

About Page

Company history and mission
Team highlights (if applicable)
Our approach to federal IT consulting

Contact Page

Contact form
Other contact methods (phone, email)

Technical Requirements

Fully responsive design
SEO best practices implemented
Fast loading times
Integration with necessary plugins (to be discussed)
Training on how to update and maintain the site
Full compliance with Web Content Accessibility Guidelines (WCAG) 2.1 Level AA
Adherence to Section 508 standards for federal website accessibility
Implementation of necessary features for ADA compliance
Updates

Designs look the same

Target Market(s)

US Federal Govt customers looking for IT support.

Industry/Entity Type

IT Consulting

Coding

Coded - Design and coding required

Colors
0054AA
0677BA
7BADD7
CADEEF
E8F1F8
0094D4
00A9DD
6FCCEA
C7EBF8
E9F6FB
00AB8E
00BBA5
67D7C9
C6EFE9
E9F9F6

```html
<!DOCTYPE html>
<html lang="en">
<head>
<meta charset="utf-8">
<title>Brisolux Federal Services</title>
<link rel="stylesheet" href="https://fonts.googleapis.com/css2?family=Poppins:wght@300;400;500;600;700&display=swap">
<style>
:root{
  --navy:#0054AA;
  --blue:#0677BA;
  --sky:#0094D4;
  --cyan:#00A9DD;
  --cyan-soft:#6FCCEA;
  --cyan-pale:#C7EBF8;
  --cyan-mist:#E9F6FB;
  --teal:#00BBA5;
  --teal-deep:#00AB8E;
  --ink:#2b2b2b;
  --text:#444;
  --white:#fff;
  --bg-soft:#f1f3f5;
}
*{box-sizing:border-box;margin:0;padding:0}
html,body{width:1200px;height:3136px;overflow:hidden}
body{font-family:"Poppins",sans-serif;color:var(--text);background:var(--white);position:relative}
.abs{position:absolute}
.btn{position:absolute;background:var(--teal);color:var(--white);font-size:16px;display:flex;align-items:center;justify-content:center;text-decoration:none}

/* header */
.site-header{position:absolute;top:0;left:0;width:1200px;height:82px;background:var(--white)}
.brand{position:absolute;display:flex;align-items:center;gap:8px;font-weight:600;color:var(--navy);letter-spacing:1px}
.brand-dot{width:30px;height:30px;border-radius:50%;background:var(--cyan)}
.main-nav{position:absolute;top:34px;left:765px;display:flex;gap:42px;font-size:14px;color:var(--ink)}
.main-nav .active{color:var(--navy)}

/* hero */
.hero{position:absolute;top:82px;left:0;width:1200px;height:572px;background:linear-gradient(100deg,#0d1b2c 0%,#17314f 45%,#284d73 70%,#1b3552 100%)}
.hero-title{position:absolute;left:72px;top:150px;font-size:61px;line-height:60px;font-weight:700;color:var(--white);letter-spacing:1px}
.hero-sub{position:absolute;left:75px;top:280px;font-size:21px;line-height:31px;color:var(--white);font-weight:400}
.slider-dots{position:absolute;top:526px;left:568px;display:flex;gap:11px}
.slider-dots span{width:8px;height:8px;background:var(--white)}
.slider-dots span.on{background:var(--teal)}

/* welcome */
.welcome-photo{position:absolute;left:95px;top:780px;width:380px;height:380px;border-radius:50%;border:20px solid var(--cyan);background:radial-gradient(circle at 45% 40%,#5d7189,#1e2d40 75%)}
.welcome h2{position:absolute;left:524px;top:756px;font-size:42px;line-height:46px;font-weight:400;color:var(--ink)}
.welcome p{position:absolute;left:524px;width:605px;font-size:15px;line-height:28px;color:var(--text)}

/* services */
.services-band{position:absolute;left:0;top:1300px}
.services-intro h2{position:absolute;left:78px;top:1320px;font-size:42px;line-height:46px;font-weight:400;color:var(--ink)}
.services-intro p{position:absolute;left:75px;top:1440px;width:240px;font-size:15px;line-height:27.3px}
.service-card{position:absolute;top:1391px;width:245px;height:284px;background:var(--white);text-align:center;box-shadow:0 2px 8px rgba(0,0,0,.12)}
.service-card svg{margin-top:33px}
.service-card h3{font-size:22px;font-weight:400;color:var(--teal-deep);margin-top:12px}
.service-card p{font-size:13.5px;line-height:23px;padding:0 16px;margin-top:6px}

/* testimonials */
.testimonials{position:absolute;top:1753px;left:0;width:1200px;height:491px;background:linear-gradient(180deg,#fff 0%,var(--bg-soft) 100%)}
.testimonials h2{position:absolute;top:68px;width:1200px;text-align:center;font-size:42px;font-weight:400;color:var(--ink)}
.testimonial{position:absolute;top:152px;width:320px;text-align:center}
.avatar{width:90px;height:90px;margin:0 auto;border-radius:50%;border:6px solid var(--cyan-soft);background:radial-gradient(circle,#9aa8b5,#53637a)}
.testimonial blockquote{margin-top:28px;font-size:15.5px;line-height:27px}
.testimonial cite{display:block;margin-top:12px;font-style:normal;font-weight:600;color:var(--sky);font-size:16.5px}

/* contact */
.contact{position:absolute;top:2244px;left:0;width:1200px;height:572px;background:linear-gradient(160deg,#0677BA 0%,#0a86cf 50%,#0094D4 100%)}
.contact h2{position:absolute;top:72px;width:1200px;text-align:center;font-size:40px;font-weight:400;color:var(--white)}
.field{position:absolute;background:var(--white);font-size:14px;color:var(--ink);padding:18px 16px}

/* footer */
.site-footer{position:absolute;top:2816px;left:0;width:1200px;height:320px;background:var(--white)}
.footer-col h4{position:absolute;font-size:20.5px;font-weight:500;color:var(--ink)}
.footer-col li{position:absolute;list-style:none;font-size:15px;color:var(--ink);white-space:nowrap}
.copyright{position:absolute;left:75px;top:180px;font-size:12px;line-height:18px}
.info-icon{position:absolute;left:794px}
.socials{position:absolute;left:794px;top:250px;display:flex;gap:16px}
.socials span{width:22px;height:22px;background:var(--navy);border-radius:3px}
</style>
</head>
<body>

<header class="site-header">
  <div class="brand" style="left:75px;top:22px;font-size:30px"><span class="brand-dot"></span>BRISOLUX</div>
  <nav class="main-nav">
    <span class="active">HOME</span><span>ABOUT</span><span>SERVICES</span><span>CONTACT</span>
  </nav>
</header>

<section class="hero" role="img" aria-label="Photo of IT engineers talking in a server room">
  <h1 class="hero-title">BRISOLUX<br>FEDERAL SERVICES</h1>
  <p class="hero-sub">Sed ut perspiciatis unde omnis iste natus error sit<br>voluptatem accusantium dolorem.</p>
  <a class="btn" style="left:75px;top:358px;width:166px;height:54px">Read More</a>
  <div class="slider-dots"><span></span><span class="on"></span><span></span><span></span></div>
</section>

<section class="welcome">
  <svg class="abs" style="left:860px;top:1080px" width="340" height="220" aria-hidden="true">
    <circle cx="300" cy="300" r="250" fill="none" stroke="var(--cyan-mist)" stroke-width="60"/>
  </svg>
  <div class="welcome-photo" role="img" aria-label="Photo of two consultants reviewing a tablet in a data center"></div>
  <h2>Welcome to<br>Brisolux Federal Services</h2>
  <p style="top:864px">Sed ut perspiciatis unde omnis iste natus error sit voluptatem accusantium oloremque laudantium, totam rem aperiam, eaque ipsa quae ab illo inventore veritatis et quasi architecto beatae vitae dicta sunt explicaboemo enim ipsam voluptatem quia voluptas sit aspernatur aut odit aut fugit, sed quia consequuntur magni dolores eos qui ratione voluptatem sequi nesciunt.</p>
  <p style="top:1016px">Sed ut perspiciatis unde omnis iste natus error sit voluptatem accusantium oloremque laudantium, totam rem aperiam, eaque ipsa quae ab illo inventore veritatis et quasi architecto beatae vitae.</p>
  <a class="btn" style="left:524px;top:1120px;width:166px;height:54px">Read More</a>
</section>

<section class="services">
  <svg class="services-band" width="1200" height="453" role="img" aria-label="Blue and teal network technology background">
    <defs><linearGradient id="band" x1="0" y1="0" x2="1" y2="1">
      <stop offset="0" stop-color="#0a3f8f"/><stop offset=".55" stop-color="#0677BA"/><stop offset="1" stop-color="#18a79a"/>
    </linearGradient></defs>
    <polygon points="552,0 1200,0 1200,453 370,453" fill="url(#band)"/>
    <path d="M1083 43 l-8 10 8 10 M1111 43 l8 10 -8 10 M1101 40 l-8 26" stroke="#fff" stroke-width="2.5" fill="none"/>
  </svg>
  <div class="services-intro">
    <h2>Our<br>Services</h2>
    <p>Sed ut perspiciatis unde omnis iste natus error sit voluptatem accusantium oloremque laudantium, totam rem aperiam, eaque ipsa quae ab illo&nbsp; inventore veritatis et quasi architecto beatae vitae dicta sunt explicab.</p>
  </div>
  <a class="btn" style="left:75px;top:1680px;width:176px;height:54px">View All Services</a>

  <article class="service-card" style="left:343px">
    <svg width="100" height="72" viewBox="0 0 100 72" fill="none" stroke="var(--navy)" stroke-width="2"><circle cx="28" cy="18" r="11"/><path d="M8 58 q0-22 20-22 q20 0 20 22z"/><circle cx="66" cy="14" r="11"/><path d="M55 14h22M66 3v22"/><path d="M48 66h46l-8-20H56z"/><circle cx="70" cy="56" r="4"/></svg>
    <h3>Nemo Enim</h3>
    <p>Sed ut perspiciatis unde omnis iste natus error sitvolu ptatem accusantium olormque laudantium</p>
  </article>
  <article class="service-card" style="left:613px">
    <svg width="100" height="72" viewBox="0 0 100 72" fill="none" stroke="var(--navy)" stroke-width="2"><rect x="10" y="2" width="26" height="20" rx="3"/><rect x="56" y="2" width="34" height="20" rx="3"/><circle cx="50" cy="30" r="8"/><circle cx="24" cy="40" r="8"/><circle cx="76" cy="40" r="8"/><path d="M8 70q0-20 16-20t16 20zM60 70q0-20 16-20t16 20z"/></svg>
    <h3>Nemo Enim</h3>
    <p>Sed ut perspiciatis unde omnis iste natus error sitvolu ptatem accusantium olormque laudantium</p>
  </article>
  <article class="service-card" style="left:883px">
    <svg width="100" height="72" viewBox="0 0 100 72" fill="none" stroke="var(--navy)" stroke-width="2"><path d="M15 20 L50 4 L85 20z"/><rect x="15" y="20" width="70" height="8"/><path d="M24 28v32M36 28v32M50 28v32M64 28v32M76 28v32"/><rect x="12" y="60" width="76" height="8"/></svg>
    <h3>Nemo Enim</h3>
    <p>Sed ut perspiciatis unde omnis iste natus error sitvolu ptatem accusantium olormque laudantium</p>
  </article>
</section>

<section class="testimonials">
  <h2>Testimonials</h2>
  <svg class="abs" style="left:45px;top:270px" width="20" height="24" aria-hidden="true"><path d="M14 2 L4 12 L14 22" stroke="#333" stroke-width="2" fill="none"/></svg>
  <svg class="abs" style="left:1135px;top:270px" width="20" height="24" aria-hidden="true"><path d="M6 2 L16 12 L6 22" stroke="#333" stroke-width="2" fill="none"/></svg>
  <div class="testimonial" style="left:78px"><div class="avatar" role="img" aria-label="Portrait of client"></div><blockquote>“ Sed ut perspiciatis unde omnis iste natus error sit voluptatem accusantium oloremque laudantium, totam rem aperiam, eaque ipsa quae..”</blockquote><cite>Name Heading</cite></div>
  <div class="testimonial" style="left:440px"><div class="avatar" role="img" aria-label="Portrait of client"></div><blockquote>“ Sed ut perspiciatis unde omnis iste natus error sit voluptatem accusantium oloremque laudantium, totam rem aperiam, eaque ipsa quae..”</blockquote><cite>Name Heading</cite></div>
  <div class="testimonial" style="left:800px"><div class="avatar" role="img" aria-label="Portrait of client"></div><blockquote>“ Sed ut perspiciatis unde omnis iste natus error sit voluptatem accusantium oloremque laudantium, totam rem aperiam, eaque ipsa quae..”</blockquote><cite>Name Heading</cite></div>
</section>

<section class="contact" role="region" aria-label="Contact form on blue digital background">
  <h2>Contact Us</h2>
  <div class="field" style="left:165px;top:156px;width:428px;height:54px">Name</div>
  <div class="field" style="left:608px;top:156px;width:429px;height:54px">Email Address</div>
  <div class="field" style="left:165px;top:225px;width:428px;height:54px">Phone No</div>
  <div class="field" style="left:608px;top:225px;width:429px;height:54px">Subject</div>
  <div class="field" style="left:165px;top:294px;width:872px;height:121px">Message</div>
  <a class="btn" style="left:387px;top:430px;width:428px;height:54px">Submit</a>
</section>

<footer class="site-footer">
  <div class="brand" style="left:75px;top:120px;font-size:28px"><span class="brand-dot"></span>BRISOLUX</div>
  <p class="copyright">Copyright © 2024. Company Name<br>All Right Reserved</p>
  <div class="footer-col">
    <h4 style="left:342px;top:64px">Site Map</h4>
    <ul><li style="left:342px;top:104px">Home</li><li style="left:342px;top:138px">About</li><li style="left:342px;top:173px">Services</li><li style="left:342px;top:207px">Contact</li></ul>
  </div>
  <div class="footer-col">
    <h4 style="left:526px;top:64px">Services</h4>
    <ul><li style="left:526px;top:104px">Sed ut perspiciatis</li><li style="left:526px;top:138px">Unde omnis iste</li><li style="left:526px;top:173px">natus error sit</li><li style="left:526px;top:207px">voluptatem accusan</li><li style="left:526px;top:242px">Doloremque</li></ul>
  </div>
  <div class="footer-col">
    <h4 style="left:794px;top:64px">Contact Info</h4>
    <svg class="info-icon" style="top:108px" width="16" height="14"><path d="M1 3l4-2 5 2 5-2v10l-5 2-5-2-4 2z" fill="var(--teal)"/></svg>
    <svg class="info-icon" style="top:166px" width="16" height="16"><path d="M4 2l3 3-2 2q2 4 4 4l2-2 3 3-2 2Q4 14 2 4z" fill="var(--teal)"/></svg>
    <svg class="info-icon" style="top:201px" width="16" height="14"><rect x="1" y="2" width="14" height="10" fill="var(--teal)"/><path d="M1 2l7 6 7-6" stroke="#fff" fill="none"/></svg>
    <ul>
      <li style="left:823px;top:104px;line-height:24px">48 Larkmoor Lane Suite 210,<br>Fairvale 22031, United States</li>
      <li style="left:823px;top:163px">+1 555-010-2468</li>
      <li style="left:823px;top:197px">info@brisoluxgrp-example.com</li>
    </ul>
  </div>
  <div class="socials" aria-label="Social links"><span></span><span></span><span></span><span></span><span></span></div>
</footer>

</body>
</html>
```